Personal training and nutrition business needs business card design

We need a business card that outlays our services and invites potential customers to join our team and take the first step to a healthier and more enjoyable life. We cater for any level of fitness and specialize in weight loss and conditioning, strength training, muscle gain and strength endurance. Whether you are just starting off or need some help getting to the next level of your journey we are here to get the job done.
We specialize in one on one or one on two personal training sessions and each program will be custom made to suit individual fitness goals of our clients

```html
<!DOCTYPE html>
<html lang="en">
<head>
<meta charset="utf-8">
<title>Stride &amp; Pulse – Business Card</title>
<link href="https://fonts.googleapis.com/css2?family=Oswald:wght@500&family=Roboto:ital,wght@0,400;0,900;1,900&display=swap" rel="stylesheet">
<style>
  :root {
    --bg: #2b2b2c;
    --card: #efefef;
    --ink: #111111;
    --text: #2e2e2e;
    --purple: #5e3a91;
    --violet: #9a4fa0;
    --grad: linear-gradient(90deg, #9a4fa0, #5e3a91);
  }
  * { margin: 0; padding: 0; box-sizing: border-box; }
  html, body { width: 1200px; height: 1138px; overflow: hidden; }
  body { background: var(--bg); position: relative; font-family: "Roboto", sans-serif; color: var(--text); }

  .card {
    position: absolute; width: 622px; height: 376px;
    background: var(--card); border-radius: 16px; overflow: hidden;
  }
  .card--front { left: 274px; top: 186px; }
  .card--back  { left: 276px; top: 607px; }

  /* front */
  .brand-mark {
    position: absolute; left: 0; right: 0; top: 120px;
    display: flex; justify-content: center; align-items: center; gap: 14px;
  }
  .brand-square { width: 30px; height: 30px; background: var(--purple); }
  .brand-name {
    font-family: "Roboto", sans-serif; font-weight: 900; font-size: 46px;
    color: var(--ink); letter-spacing: 1px; line-height: 1;
  }
  .tagline {
    position: absolute; left: 0; right: 0; top: 250px; text-align: center;
    font-family: "Oswald", sans-serif; font-weight: 500; font-size: 14px;
    letter-spacing: 1.2px; color: var(--violet);
  }
  .site-row {
    position: absolute; left: 0; right: 0; top: 322px;
    display: flex; justify-content: center; align-items: center; gap: 18px;
    font-size: 16px; color: var(--ink);
  }
  .site-row .rule { width: 70px; height: 2px; background: var(--ink); }
  .accent { color: var(--violet); }
  .accent-dark { color: var(--purple); }
  .front-band { position: absolute; left: 0; right: 0; bottom: 0; height: 10px; background: var(--grad); }

  /* back */
  .back-brand {
    position: absolute; left: 62px; top: 110px; width: 220px;
    text-align: center;
  }
  .back-brand .brand-square { margin: 0 auto 18px; width: 36px; height: 36px; }
  .back-brand .brand-name { font-size: 40px; line-height: 1.05; }

  .contact { position: absolute; left: 342px; top: 70px; }
  .person-name {
    font-weight: 900; font-style: italic; font-size: 25px; letter-spacing: 1px;
    color: var(--purple); line-height: 1;
  }
  .person-role { margin-top: 9px; font-size: 16px; }
  .contact-list { list-style: none; margin-top: 34px; }
  .contact-list li { display: flex; align-items: center; gap: 14px; font-size: 16px; height: 24px; }
  .contact-list svg { width: 14px; height: 14px; fill: var(--purple); flex: none; }
  .address { margin-top: 8px; font-size: 16px; line-height: 24px; }

  .back-strip { position: absolute; left: 0; bottom: 0; width: 300px; height: 16px; background: var(--grad); }
  .back-tab {
    position: absolute; right: 0; bottom: 0; width: 366px; height: 47px;
    background: var(--purple);
    clip-path: polygon(24px 0, 100% 0, 100% 100%, 0 100%);
    border-top-left-radius: 14px;
    display: flex; align-items: center; justify-content: flex-end; padding-right: 19px;
    color: #f2eaf6; font-size: 15.5px;
  }
</style>
</head>
<body>

<section class="card card--front">
  <div class="brand-mark">
    <span class="brand-square"></span>
    <span class="brand-name">STRIDE &amp; PULSE</span>
  </div>
  <p class="tagline">PERSONAL TRAINING.&nbsp; NUTRITION. MOTIVATION</p>
  <div class="site-row">
    <span class="rule"></span>
    <span>www.<span class="accent">stride</span>and<span class="accent-dark">pulse</span>.com</span>
    <span class="rule"></span>
  </div>
  <div class="front-band"></div>
</section>

<section class="card card--back">
  <div class="back-brand">
    <div class="brand-square"></div>
    <div class="brand-name">STRIDE<br>&amp; PULSE</div>
  </div>

  <div class="contact">
    <h1 class="person-name">MARCUS VALE</h1>
    <p class="person-role">Personal Trainer</p>
    <ul class="contact-list">
      <li>
        <svg viewBox="0 0 16 16" aria-hidden="true"><path d="M2 5c0-2 2-3 6-3s6 1 6 3v1h-3V5H5v1H2zM4 7h8l2 6H2z"/></svg>
        +12 (345) 555-0148
      </li>
      <li>
        <svg viewBox="0 0 16 16" aria-hidden="true"><path d="M1 3h14v10H1zM2.5 4.5 8 9l5.5-4.5v7h-11z" fill-rule="evenodd"/></svg>
        marcus@strideandpulse.com
      </li>
      <li>
        <svg viewBox="0 0 16 16" aria-hidden="true"><path d="M8 1a7 7 0 1 0 0 14A7 7 0 0 0 8 1zm0 1.5c.8 0 1.7 1.6 2 4H6c.3-2.4 1.2-4 2-4zM6 9.5h4c-.3 2.4-1.2 4-2 4s-1.7-1.6-2-4zM2.6 6.5h2c-.1 1 0 2 0 3h-2a5.6 5.6 0 0 1 0-3zm8.8 0h2a5.6 5.6 0 0 1 0 3h-2c.1-1 .1-2 0-3z"/></svg>
        <span>www.<span class="accent-dark">stride</span>and<span class="accent">pulse</span>.com</span>
      </li>
    </ul>
    <p class="address">2140 Cedar Ridge Lane<br>Fairview Texas 75069</p>
  </div>

  <div class="back-strip"></div>
  <div class="back-tab">Personal Training | Nutrition | Motivation</div>
</section>

</body>
</html>
```